SkyvornQ Business Cards and Stationary Design

Need a design for our business cards and stationary. I want to carry on the theme of the logo. I want the business cards to have a design on the back. I would like the business cards and the stationary to carry the same theme, design scheme, and branding

Target Market(s)

Airlines and Maintenance Facilities

Industry/Entity Type

Aviation

Contact Information for Business Card

Name
Position Title
Address: 4827 Trellis Hollow Road, Fort Pierce, Florida, 34951
Office Number
Mobile Number
Email
Website

Font styles to use
Serif
Sans Serif

Colors

Designer to choose colors to be used in the design.

```html
<!DOCTYPE html>
<html lang="en">
<head>
<meta charset="utf-8">
<title>SkyvornQ Business Card</title>
<link rel="stylesheet" href="https://fonts.googleapis.com/css2?family=Ubuntu:wght@400;500&display=swap">
<style>
  :root {
    --backdrop: #dcd7d1;
    --card: #eef1f3;
    --sky-blue: #1a8fc4;
    --bright-blue: #23a6d5;
    --navy: #1c2b45;
    --ink: #2a2f3a;
    --band-text: #d8dde5;
  }
  * { margin: 0; padding: 0; box-sizing: border-box; }
  html, body {
    width: 1200px;
    height: 1054px;
    overflow: hidden;
    background: var(--backdrop);
    font-family: "Ubuntu", sans-serif;
  }
  .business-card {
    position: absolute;
    left: 100px;
    top: 225px;
    width: 1000px;
    height: 604px;
    background: var(--card);
    box-shadow: 0 10px 30px rgba(0, 0, 0, 0.12);
    overflow: hidden;
  }
  .card-band {
    position: absolute;
    left: 0;
    top: 0;
    width: 1000px;
    height: 604px;
  }
  .brand-name {
    position: absolute;
    left: 62px;
    top: 238px;
    width: 448px;
    text-align: center;
    font-size: 50px;
    font-weight: 500;
    color: var(--navy);
    line-height: 1;
  }
  .holder-name {
    position: absolute;
    left: 603px;
    top: 124px;
    font-size: 42px;
    font-weight: 500;
    color: var(--sky-blue);
    letter-spacing: 0.5px;
  }
  .holder-title {
    position: absolute;
    left: 604px;
    top: 178px;
    font-size: 23px;
    font-weight: 400;
    color: var(--ink);
  }
  .contact-list {
    position: absolute;
    left: 608px;
    top: 250px;
    list-style: none;
  }
  .contact-item {
    display: flex;
    align-items: center;
    height: 33px;
    font-size: 24px;
    color: var(--ink);
  }
  .contact-icon {
    width: 22px;
    height: 22px;
    margin-right: 20px;
    fill: var(--sky-blue);
  }
  .postal-address {
    position: absolute;
    left: 604px;
    top: 357px;
    font-size: 24px;
    line-height: 33px;
    font-style: normal;
    color: var(--ink);
  }
  .website {
    position: absolute;
    left: 604px;
    top: 559px;
    font-size: 23px;
    color: var(--band-text);
    letter-spacing: 0.5px;
  }
</style>
</head>
<body>
  <main class="business-card">
    <svg class="card-band" viewBox="0 0 1000 604" aria-hidden="true">
      <rect x="0" y="582" width="520" height="22" fill="var(--bright-blue)"/>
      <path d="M504 542 H1000 V604 H460 Q490 590 504 542 Z" fill="var(--navy)"/>
    </svg>

    <div class="brand-name">SkyvornQ</div>

    <h1 class="holder-name">Marcus Delhaven</h1>
    <p class="holder-title">Managing Director</p>

    <ul class="contact-list">
      <li class="contact-item">
        <svg class="contact-icon" viewBox="0 0 24 24" aria-label="Office"><path d="M3 8c0-2 4-4 9-4s9 2 9 4v2h-5V8c-1-.6-2.5-1-4-1s-3 .4-4 1v2H3z M6 12h12l2 8H4z"/></svg>
        2468 1357 902
      </li>
      <li class="contact-item">
        <svg class="contact-icon" viewBox="0 0 24 24" aria-label="Mobile"><path d="M7 2h10a1 1 0 0 1 1 1v18a1 1 0 0 1-1 1H7a1 1 0 0 1-1-1V3a1 1 0 0 1 1-1z M8.5 5v12h7V5z M12 18.5a1 1 0 1 0 0 2a1 1 0 0 0 0-2z"/></svg>
        9876 5432 110
      </li>
      <li class="contact-item">
        <svg class="contact-icon" viewBox="0 0 24 24" aria-label="Email"><path d="M2 6h20v12H2z M3.5 7.5 12 13l8.5-5.5v-.1H3.5z" fill-rule="evenodd"/></svg>
        marcus@skyvornq.com
      </li>
    </ul>

    <address class="postal-address">4827 Trellis Hollow Road,<br>Fort Pierce, FL 34951</address>

    <p class="website">www.skyvornq.com</p>
  </main>
</body>
</html>
```